Dovetree baby skincare

design business cards (double sided) and complimentary note (single sided)

Industry/Entity Type

Business

Colors

Designer to choose colors to be used in the design.

```html
<!DOCTYPE html>
<html lang="en">
<head>
<meta charset="utf-8">
<title>Dovetree baby skincare – Complimentary Note</title>
<link rel="stylesheet" href="https://fonts.googleapis.com/css2?family=Open+Sans:ital,wght@0,400;1,400&display=swap">
<style>
  :root {
    --backdrop: #9a9a9a;
    --paper: #f2f2f2;
    --peach: #f1c3a8;
    --peach-light: #f7ddcc;
    --ink-grey: #4a4a4a;
  }
  html, body {
    margin: 0;
    padding: 0;
    width: 1200px;
    height: 800px;
    overflow: hidden;
    background: var(--backdrop);
  }
  .canvas {
    position: relative;
    width: 1200px;
    height: 800px;
  }
  .note-sheet {
    position: absolute;
    left: 100px;
    top: 40px;
    width: 1000px;
    height: 720px;
    background: var(--paper);
    box-shadow: 0 2px 10px rgba(0,0,0,0.2);
    overflow: hidden;
  }
  .watercolour-wash {
    position: absolute;
    top: 150px;
    right: 0;
    width: 300px;
    height: 84px;
    border-radius: 60px 0 0 40px / 42px 0 0 42px;
    background: linear-gradient(90deg, var(--peach) 0%, var(--peach) 55%, var(--peach-light) 100%);
    opacity: 0.85;
  }
  .brand-name {
    position: absolute;
    top: 64px;
    right: 48px;
    margin: 0;
    font-family: "Open Sans", sans-serif;
    font-weight: 400;
    font-size: 56px;
    line-height: 1;
    color: var(--ink-grey);
  }
  .web-address {
    position: absolute;
    bottom: 96px;
    left: 0;
    width: 100%;
    margin: 0;
    text-align: center;
    font-family: "Open Sans", sans-serif;
    font-style: italic;
    font-size: 20px;
    color: var(--ink-grey);
  }
</style>
</head>
<body>
  <div class="canvas">
    <div class="note-sheet">
      <div class="watercolour-wash" role="img" aria-label="Soft peach watercolour brush stroke"></div>
      <p class="brand-name">dovetree</p>
      <p class="web-address">www.dovetreeskincare.com</p>
    </div>
  </div>
</body>
</html>
```